Kelvaro.ch is looking for business card letterhead and envelope C5 with WOW effect

We need a strong business card for our company Kelvaro.ch, logo is available. You want a black or dark background on which the logo Stark r% 26 # 252; appears. Letterhead and envelope in C5 format should be in a similar design, but does not have to be We need a strong business card for our company Kelvaro.ch, logo is available. A black or dark background is desired, on which the logo Stark comes across. The letterhead and the envelope in C5 format should have a similar design.

Target Market(s)

Private customers as well as entrepreneurs

Contact Information for Business Card

E-mail: info@kelvaro-example.ch
Web.www.Kelvaro-example.ch
Tel: +41 ( 0 ) 79 482 6037
Adresse:
Lindenweg 14
9406 Tarnbach

Hier kann man Icons verwenden für Email,Tel und Adressse

Font styles to use
Other font styles liked:
• Dubai,bold

Colors

Designer to choose colors to be used in the design.

Requirements
Must have
• WOW effect
Nice to have
• R% 26 # 252; back business card with our service listings. - VEHICLE LABELING - SHOP WINDOW LABELING - STICKERS AND MUCH MORE ... in red color

```html
<!DOCTYPE html>
<html lang="en">
<head>
<meta charset="utf-8">
<title>Kelvaro.ch – Business Card</title>
<link rel="stylesheet" href="https://fonts.googleapis.com/css2?family=Open+Sans:wght@400;600;700&display=swap">
<style>
  :root {
    --stage: #2a2a2a;
    --card: #141414;
    --card-edge: #1e1e1e;
    --yellow: #f7c21a;
    --red: #d8322f;
    --white: #ffffff;
    --soft: #e6e6e6;
  }
  * { margin: 0; padding: 0; box-sizing: border-box; }
  html, body { width: 1200px; height: 852px; overflow: hidden; }
  body {
    background: var(--stage);
    font-family: "Open Sans", Arial, sans-serif;
    position: relative;
  }
  .card {
    position: absolute;
    left: 290px;
    width: 620px;
    height: 354px;
    border-radius: 16px;
    background: linear-gradient(135deg, var(--card-edge), var(--card));
    box-shadow: 0 10px 30px rgba(0,0,0,.5);
    color: var(--white);
  }
  .card--front { top: 48px; }
  .card--back { top: 450px; }

  .wordmark {
    display: flex;
    align-items: center;
    gap: 14px;
    font-weight: 700;
    color: var(--white);
    letter-spacing: .5px;
  }
  .wordmark__square {
    display: inline-block;
    background: var(--yellow);
  }

  .card--front .wordmark {
    position: absolute;
    left: 0; right: 0; top: 118px;
    justify-content: center;
    font-size: 44px;
  }
  .card--front .wordmark__square { width: 40px; height: 40px; }
  .services {
    position: absolute;
    left: 0; right: 0; top: 210px;
    text-align: center;
    color: var(--red);
    font-size: 15px;
    font-weight: 600;
    letter-spacing: 1px;
    line-height: 1.45;
    text-transform: uppercase;
  }

  .card--back .wordmark {
    position: absolute;
    left: 40px; top: 44px;
    font-size: 34px;
  }
  .card--back .wordmark__square { width: 30px; height: 30px; }
  .person {
    position: absolute;
    left: 40px; top: 150px;
  }
  .person__name {
    color: var(--yellow);
    font-size: 24px;
    font-weight: 600;
    text-transform: uppercase;
    letter-spacing: .3px;
  }
  .person__role {
    color: var(--soft);
    font-size: 15px;
    margin-top: 2px;
  }
  .divider {
    position: absolute;
    left: 40px; top: 222px;
    width: 340px; height: 2px;
    background: var(--yellow);
  }
  .contact {
    position: absolute;
    left: 40px; top: 240px;
    font-size: 15px;
    color: var(--soft);
    line-height: 1.7;
  }
  .contact__label { color: var(--yellow); font-weight: 700; margin-right: 4px; }
  .contact__row span + span { margin-left: 18px; }
  .website {
    position: absolute;
    right: 36px; top: 211px;
    color: var(--yellow);
    font-size: 14px;
    font-weight: 700;
    white-space: nowrap;
  }
</style>
</head>
<body>
  <section class="card card--front">
    <div class="wordmark">
      <span class="wordmark__square"></span>
      <span class="wordmark__name">KELVARO.CH</span>
    </div>
    <p class="services">
      Vehicle labeling | Shop window labeling<br>
      Stickers and much more
    </p>
  </section>

  <section class="card card--back">
    <div class="wordmark">
      <span class="wordmark__square"></span>
      <span class="wordmark__name">KELVARO.CH</span>
    </div>
    <div class="person">
      <p class="person__name">Marco Brenner</p>
      <p class="person__role">Director</p>
    </div>
    <div class="divider"></div>
    <p class="website">www.Kelvaro-example.ch</p>
    <div class="contact">
      <p class="contact__row">
        <span><b class="contact__label">P:</b>+41 ( 0 ) 79 482 6037</span>
        <span><b class="contact__label">E:</b>info@kelvaro-example.ch</span>
      </p>
      <p class="contact__row">Lindenweg 14 9406 Tarnbach</p>
    </div>
  </section>
</body>
</html>
```